Roofing Company Modern look

I want a modern and sophisticated look for our roofing business.

Our address is :

5217 Mallow Creek Ln
Orlando, Fl 32825

(407)-583-2196

www.HarborlineRoofsFl.com

I also want to make sure on the back there is a spot to put
Project Manager Name :

Number:

Because the cards will be used by all sales people

Project Manager Name :

Also there are accreditation we have logos are uploaded here as well that I would like maybe on the back of card as well

I also want to highlight our special attributions or trades:

Residential & Commercial
Fully Insured
License # CCC7482913
Insurance Claims
Serving Central Florida Since 1992
Free Estimates

Contact Information for Business Card

Our address is :

5217 Mallow Creek Ln
Orlando, Fl 32825

(407)-583-2196

Project Manager Name :

Residential & Commercial
Fully Insured
License # CCC7482913
Insurance Claims
Free Estimates

Font styles to use
Serif
Sans Serif

Colors
3176b5

Requirements
Must have
• Must have royal blue like my logo grey and black are the colors I like

```html
<!DOCTYPE html>
<html lang="en">
<head>
<meta charset="utf-8">
<title>Harborline Roofs &amp; Gutters – Business Card</title>
<link rel="stylesheet" href="https://fonts.googleapis.com/css2?family=Questrial&family=Roboto+Condensed:wght@400;700&display=swap">
<style>
  :root {
    --royal-blue: #3176b5;
    --deep-blue: #1f68ad;
    --sky-blue: #4aa6db;
    --charcoal: #3a3a3a;
    --text-grey: #4a4a4a;
    --badge-red: #d8262e;
    --badge-navy: #1d3a6e;
    --page: #e4e4e4;
    --card: #ffffff;
  }
  * { margin: 0; padding: 0; box-sizing: border-box; }
  html, body { width: 1200px; height: 1200px; overflow: hidden; background: var(--page); }
  .canvas { position: relative; width: 1200px; height: 1200px; }

  .card {
    position: absolute;
    left: 262px;
    width: 800px;
    height: 457px;
    background: var(--card);
    border-radius: 26px;
    overflow: hidden;
    transform: scale(0.8575);
    transform-origin: top left;
    box-shadow: 0 12px 28px rgba(0,0,0,0.18);
  }
  .card--front { top: 165px; }
  .card--back { top: 653px; }
  .card svg.swoosh { position: absolute; left: 0; top: 0; width: 800px; height: 457px; }

  /* front */
  .brand { position: absolute; left: 54px; top: 40px; width: 280px; text-align: center; }
  .brand__mark { width: 92px; height: 92px; border-radius: 50%; background: var(--royal-blue); margin: 0 auto 18px; }
  .brand__name, .brand__tag { font-family: "Questrial", sans-serif; color: var(--royal-blue); letter-spacing: 2px; }
  .brand__name { font-size: 40px; line-height: 1; text-transform: uppercase; }
  .brand__tag { font-size: 15px; margin-top: 6px; text-transform: uppercase; }

  .badges { position: absolute; display: flex; gap: 8px; align-items: center; }
  .badges--front { left: 585px; top: 44px; }
  .badge-square { width: 44px; height: 56px; border: 2px solid var(--badge-navy); border-radius: 4px; background: #f2f5fa; }
  .badge-hex { width: 62px; height: 56px; background: var(--charcoal); clip-path: polygon(50% 0, 100% 25%, 100% 75%, 50% 100%, 0 75%, 0 25%); }
  .badge-round { width: 54px; height: 54px; border-radius: 50%; border: 5px solid #8a8a8a; background: #f4f4f4; }
  .badge-bar { position: absolute; height: 46px; border: 2px solid var(--badge-navy); background: linear-gradient(90deg, var(--badge-red) 0 26%, #fff 26% 100%); }
  .badge-bar--front { left: 593px; top: 114px; width: 163px; }

  .address { position: absolute; right: 42px; top: 255px; text-align: right; font-family: "Questrial", sans-serif; color: #fff; }
  .address span { display: block; }
  .address__street { font-size: 24px; line-height: 31px; }
  .address__city { font-size: 28px; line-height: 33px; }

  .phone-band {
    position: absolute; left: 420px; top: 330px; width: 380px; height: 57px;
    background: #fff; border-radius: 29px 0 0 29px; display: flex; align-items: center;
  }
  .phone-band__icon { width: 50px; height: 50px; border-radius: 50%; background: var(--charcoal); margin-left: 5px; display: flex; align-items: center; justify-content: center; }
  .phone-band__number { margin-left: 14px; font-family: "Roboto Condensed", sans-serif; font-weight: 700; font-size: 40px; color: var(--royal-blue); letter-spacing: 0.5px; }

  .website { position: absolute; right: 42px; font-family: "Questrial", sans-serif; font-size: 21px; color: #fff; }
  .website--front { top: 395px; }
  .website--back { top: 406px; }

  /* back */
  .field { position: absolute; left: 62px; right: 62px; display: flex; align-items: flex-end; font-family: "Roboto Condensed", sans-serif; font-size: 19px; color: var(--royal-blue); text-transform: uppercase; }
  .field__line { flex: 1; border-bottom: 1px solid var(--royal-blue); margin-left: 6px; margin-bottom: 4px; }
  .field--manager { top: 55px; }
  .field--phone { top: 118px; }

  .features { position: absolute; top: 172px; list-style: none; font-family: "Roboto Condensed", sans-serif; font-size: 22px; color: var(--text-grey); }
  .features--left { left: 62px; }
  .features--right { left: 392px; }
  .features li { position: relative; padding-left: 32px; line-height: 26.5px; }
  .features li::before { content: ""; position: absolute; left: 4px; top: 7px; width: 13px; height: 13px; border-radius: 50%; background: var(--royal-blue); }

  .badges--back { left: 56px; top: 290px; }
  .badge-bar--back { left: 66px; top: 368px; width: 148px; height: 42px; }
</style>
</head>
<body>
<main class="canvas">

  <section class="card card--front" aria-label="Business card front">
    <svg class="swoosh" viewBox="0 0 800 457" aria-hidden="true">
      <defs>
        <linearGradient id="frontBlue" x1="0" y1="1" x2="1" y2="0">
          <stop offset="0" stop-color="#1c62a8"/>
          <stop offset="0.55" stop-color="#3a95d0"/>
          <stop offset="1" stop-color="#2f86c6"/>
        </linearGradient>
      </defs>
      <path d="M0,457 L0,450 C190,300 470,185 800,212 L800,457 Z" fill="url(#frontBlue)"/>
      <path d="M8,446 C200,288 470,172 800,205" fill="none" stroke="#3a3a3a" stroke-width="6"/>
      <path d="M30,445 C220,300 480,200 800,222" fill="none" stroke="#8cc8ec" stroke-width="3" opacity="0.7"/>
    </svg>

    <div class="brand">
      <div class="brand__mark"></div>
      <p class="brand__name">Harborline</p>
      <p class="brand__tag">Roofs &amp; Gutters Inc.</p>
    </div>

    <div class="badges badges--front" aria-label="Accreditation badges">
      <div class="badge-square"></div>
      <div class="badge-hex"></div>
      <div class="badge-round"></div>
    </div>
    <div class="badge-bar badge-bar--front" aria-hidden="true"></div>

    <address class="address">
      <span class="address__street">5217 Mallow Creek Ln</span>
      <span class="address__city">Orlando, Fl 32825</span>
    </address>

    <div class="phone-band">
      <div class="phone-band__icon">
        <svg width="26" height="26" viewBox="0 0 24 24" aria-hidden="true"><path fill="#fff" d="M6.6 10.8a15.1 15.1 0 0 0 6.6 6.6l2.2-2.2c.3-.3.7-.4 1-.2 1.1.4 2.3.6 3.6.6.6 0 1 .4 1 1V20c0 .6-.4 1-1 1A17 17 0 0 1 3 4c0-.6.4-1 1-1h3.5c.6 0 1 .4 1 1 0 1.3.2 2.5.6 3.6.1.3 0 .7-.2 1z"/></svg>
      </div>
      <span class="phone-band__number">(407)-583-2196</span>
    </div>

    <p class="website website--front">www.HarborlineRoofsFl.com</p>
  </section>

  <section class="card card--back" aria-label="Business card back">
    <svg class="swoosh" viewBox="0 0 800 457" aria-hidden="true">
      <defs>
        <linearGradient id="backBlue" x1="0" y1="1" x2="1" y2="0">
          <stop offset="0" stop-color="#1c62a8"/>
          <stop offset="0.6" stop-color="#3a95d0"/>
          <stop offset="1" stop-color="#2f86c6"/>
        </linearGradient>
      </defs>
      <path d="M230,457 C380,380 560,335 800,352 L800,457 Z" fill="url(#backBlue)"/>
      <path d="M225,457 C380,372 560,326 800,344" fill="none" stroke="#3a3a3a" stroke-width="5"/>
    </svg>

    <div class="field field--manager"><span>Project Manager Name :</span><span class="field__line"></span></div>
    <div class="field field--phone"><span>Phone:</span><span class="field__line"></span></div>

    <ul class="features features--left">
      <li>Residential &amp; Commercial</li>
      <li>Fully Insured</li>
      <li>License # CCC7482913</li>
    </ul>
    <ul class="features features--right">
      <li>Insurance Claims</li>
      <li>Serving Central Florida Since 1992</li>
      <li>Free Estimates</li>
    </ul>

    <div class="badges badges--back" aria-label="Accreditation badges">
      <div class="badge-square"></div>
      <div class="badge-hex"></div>
      <div class="badge-round"></div>
    </div>
    <div class="badge-bar badge-bar--back" aria-hidden="true"></div>

    <p class="website website--back">www.HarborlineRoofsFl.com</p>
  </section>

</main>
</body>
</html>
```